New Innovative Counselling and psychotherapy Service needs Business Card design

Keep it simple and professional. On one side, just company name and logo (perhaps in all blue) and maybe a tag line.

On other side (all white) my name and Qualifications in centre

Industry/Entity Type

Health And Wellness

Contact Information for Business Card

Dara Whelby
Counsellor & Psychotherapist
BSc (Psychol.), BA, Dip. (Couns. & Psych.), PG.Cert (CBT), FGTrK, ONRE

I will also require Mobile no, Email and web site address of which I'll pass on to final designer.

Font styles to use
Sans Serif

Requirements
Must have
• My Logo Only and please use the colours in logo that is in it.
Should not have
• Any other images

```html
<!DOCTYPE html>
<html lang="en">
<head>
<meta charset="utf-8">
<title>Kindwell Lane – Business Card</title>
<link rel="stylesheet" href="https://fonts.googleapis.com/css2?family=Open+Sans:wght@400;600;700&display=swap">
<style>
  :root {
    --stage: #e9ebee;
    --card-white: #ffffff;
    --brand-blue: #3fb0ea;
    --brand-green: #93d35a;
    --green-soft: #a8dc78;
    --ink: #2f2f33;
    --ink-soft: #4a4a50;
    --social-blue: #2f5f9e;
  }
  * { box-sizing: border-box; margin: 0; padding: 0; }
  html, body {
    width: 1200px; height: 782px; overflow: hidden;
    background: var(--stage);
    font-family: "Open Sans", sans-serif;
  }
  .stage {
    position: relative; width: 1200px; height: 782px;
    display: flex; align-items: center; justify-content: center; gap: 30px;
  }
  .card {
    position: relative; width: 560px; height: 320px; overflow: hidden;
    box-shadow: 0 6px 18px rgba(0,0,0,.18);
  }
  /* Front */
  .card--front { background: var(--card-white); }
  .social { position: absolute; top: 16px; left: 18px; display: flex; gap: 5px; }
  .social__dot { width: 15px; height: 15px; border-radius: 50%; background: var(--social-blue); }
  .brand {
    position: absolute; top: 104px; left: 262px;
    display: flex; align-items: center; gap: 12px;
  }
  .brand__dot { width: 46px; height: 46px; border-radius: 50%; background: var(--brand-blue); }
  .brand__name { font-size: 30px; font-weight: 400; color: var(--ink); letter-spacing: -.3px; }
  .person { position: absolute; top: 118px; left: 22px; line-height: 1.25; }
  .person__name { font-size: 17px; font-weight: 400; letter-spacing: .3px; }
  .person__first { color: var(--brand-blue); }
  .person__last { color: var(--brand-green); }
  .person__role, .person__quals { font-size: 13px; color: var(--ink); }
  .contact {
    position: absolute; right: 22px; top: 202px; text-align: right;
    font-size: 14px; color: var(--ink); line-height: 1.3;
  }
  .contact__line { display: flex; justify-content: flex-end; align-items: center; gap: 5px; }
  .contact__icon { width: 11px; height: 11px; fill: var(--brand-blue); }
  .tagline {
    position: absolute; left: 22px; top: 270px;
    font-size: 11.5px; font-weight: 700; color: var(--brand-blue); letter-spacing: .3px;
  }
  .band { position: absolute; left: 0; bottom: 0; width: 560px; height: 30px; }
  /* Back */
  .card--back { background: var(--brand-green); }
  .pattern {
    position: absolute; inset: 0;
    background: linear-gradient(135deg, var(--green-soft) 0%, var(--brand-green) 100%);
  }
  .back-brand {
    position: absolute; top: 140px; right: 70px;
    display: flex; align-items: center; gap: 10px;
  }
  .back-brand__dot { width: 34px; height: 34px; border-radius: 50%; background: var(--card-white); }
  .back-brand__name { font-size: 20px; font-weight: 400; color: var(--card-white); }
</style>
</head>
<body>
<main class="stage">
  <section class="card card--front" aria-label="Card front">
    <div class="social" aria-label="Social profiles">
      <span class="social__dot"></span><span class="social__dot"></span>
      <span class="social__dot"></span><span class="social__dot"></span>
    </div>

    <div class="brand">
      <span class="brand__dot"></span>
      <span class="brand__name">Kindwell Lane</span>
    </div>

    <div class="person">
      <p class="person__name"><span class="person__first">DARA</span> <span class="person__last">WHELBY</span></p>
      <p class="person__role">Counsellor &amp; Psychotherapist</p>
      <p class="person__quals">BSc (Psychol.), BA,</p>
      <p class="person__quals">Dip. (Couns. &amp; Psych.),</p>
      <p class="person__quals">PG.Cert (CBT), FGTrK, ONRE</p>
    </div>

    <div class="contact">
      <p class="contact__line">086 5402 917
        <svg class="contact__icon" viewBox="0 0 12 12"><path d="M2.5 1l2 2.4-1 1.2a7 7 0 0 0 3.9 3.9l1.2-1 2.4 2-1 1.5C6 11 1 6 1 2.5z"/></svg></p>
      <p class="contact__line">info@kindwelllane.com
        <svg class="contact__icon" viewBox="0 0 12 12"><path d="M1 2.5h10v7H1z M1 2.5l5 4 5-4" fill="none" stroke="var(--brand-blue)" stroke-width="1.4"/></svg></p>
      <p class="contact__line">www.kindwelllane.com
        <svg class="contact__icon" viewBox="0 0 12 12"><circle cx="6" cy="6" r="5"/></svg></p>
    </div>

    <p class="tagline">CARING FOR YOUR PSYCHOLOGICAL WELL-BEING IS OUR TOP PRIORITY</p>

    <svg class="band" viewBox="0 0 560 30" aria-hidden="true">
      <polygon points="0,18 300,18 288,30 0,30" fill="var(--brand-blue)"/>
      <polygon points="306,12 560,12 560,30 294,30" fill="var(--brand-green)"/>
    </svg>
  </section>

  <section class="card card--back" aria-label="Card back">
    <div class="pattern" role="img" aria-label="Repeating light green leaf pattern across the card"></div>
    <div class="back-brand">
      <span class="back-brand__dot"></span>
      <span class="back-brand__name">Kindwell Lane</span>
    </div>
  </section>
</main>
</body>
</html>
```